Vale Crest - Business Cards

We are a consultancy to help builders to optimize their planning in order to save building costs. For that reason we need a clean and professional business card for our high-priced services. A QR code should lead to the contact information needed.

```html
<!DOCTYPE html>
<html lang="en">
<head>
<meta charset="utf-8">
<title>Vale Crest – Business Cards</title>
<link href="https://fonts.googleapis.com/css2?family=Roboto:wght@400;500;700&family=Roboto+Condensed:wght@500;700&display=swap" rel="stylesheet">
<style>
  :root{
    --bg:#2a2a2b;
    --gold-light:#e6c062;
    --gold-mid:#c9973e;
    --gold-dark:#a5682a;
    --ink:#2f2f33;
    --ink-soft:#3c3c40;
    --paper:#f1f1f1;
    --paper-shade:#e2e2e2;
  }
  html,body{margin:0;padding:0;}
  body{
    width:1200px;height:1138px;overflow:hidden;
    background:var(--bg);
    position:relative;
    font-family:"Roboto",Arial,sans-serif;
  }
  .card{
    position:absolute;
    border-radius:16px;
    overflow:hidden;
    box-shadow:0 4px 12px rgba(0,0,0,.45);
  }
  .card-front{
    left:274px;top:186px;width:623px;height:376px;
    background:linear-gradient(200deg,var(--gold-light) 0%,var(--gold-mid) 55%,var(--gold-dark) 100%);
    display:flex;align-items:center;justify-content:center;
  }
  .brand-name{
    font-family:"Roboto Condensed","Roboto",Arial,sans-serif;
    font-weight:700;
    color:var(--ink);
    text-transform:uppercase;
    letter-spacing:2px;
    margin:0;
    line-height:1;
  }
  .card-front .brand-name{font-size:50px;}
  .card-back{
    left:276px;top:608px;width:618px;height:374px;
    background:linear-gradient(180deg,var(--paper) 0%,var(--paper-shade) 100%);
  }
  .back-shapes{position:absolute;left:0;top:0;}
  .contact{
    position:absolute;left:30px;top:86px;
    color:var(--ink-soft);
  }
  .contact-name{
    font-family:"Roboto Condensed","Roboto",Arial,sans-serif;
    font-weight:700;font-size:25px;margin:0;color:var(--ink);line-height:1.1;
  }
  .contact-role{font-size:16px;margin:2px 0 0;line-height:1.2;}
  .contact-list{list-style:none;margin:24px 0 0;padding:0;font-size:17px;}
  .contact-list li{display:flex;align-items:center;height:24px;}
  .contact-list svg{width:14px;height:14px;margin-right:18px;flex:none;}
  .contact-address{font-size:17px;margin:8px 0 0;line-height:24px;}
  .back-brand{
    position:absolute;left:362px;top:192px;width:236px;
    text-align:center;
  }
  .back-brand .brand-name{font-size:28px;}
</style>
</head>
<body>

<section class="card card-front" aria-label="Card front">
  <p class="brand-name">Vale Crest</p>
</section>

<section class="card card-back" aria-label="Card back">
  <svg class="back-shapes" width="618" height="374" viewBox="0 0 618 374">
    <defs>
      <linearGradient id="goldPanel" x1="0" y1="0" x2="0" y2="1">
        <stop offset="0" stop-color="var(--gold-dark)"/>
        <stop offset="0.5" stop-color="var(--gold-light)"/>
        <stop offset="1" stop-color="var(--gold-dark)"/>
      </linearGradient>
    </defs>
    <path d="M328,0 Q212,187 352,374 L618,374 L618,0 Z" fill="#2c2c33"/>
    <path d="M356,0 Q218,187 352,374 L618,374 L618,0 Z" fill="url(#goldPanel)"/>
  </svg>

  <div class="contact">
    <h2 class="contact-name">Vale Crest</h2>
    <p class="contact-role">Managing Director</p>
    <ul class="contact-list">
      <li>
        <svg viewBox="0 0 14 14" aria-hidden="true"><path d="M1 4 Q7 0 13 4 L11 6 L9 5 L5 5 L3 6 Z M3 7 L11 7 L12 12 L2 12 Z" fill="var(--gold-mid)"/></svg>
        555-010-2040
      </li>
      <li>
        <svg viewBox="0 0 14 14" aria-hidden="true"><rect x="1" y="3" width="12" height="9" fill="var(--gold-mid)"/><path d="M1 3 L7 8 L13 3" fill="none" stroke="#fff" stroke-width="1"/></svg>
        hello@valecrest.com
      </li>
      <li>
        <svg viewBox="0 0 14 14" aria-hidden="true"><circle cx="7" cy="7" r="6" fill="var(--gold-mid)"/><path d="M1 7 H13 M7 1 V13 M7 1 Q3 7 7 13 M7 1 Q11 7 7 13" fill="none" stroke="#fff" stroke-width=".8"/></svg>
        www.valecrest.com
      </li>
    </ul>
    <p class="contact-address">234 Anywhere St., Any City,<br>Any Town, US 123456</p>
  </div>

  <div class="back-brand">
    <p class="brand-name">Vale Crest</p>
  </div>
</section>

</body>
</html>
```